Flyer for the Lumen 2025 Conference

I am looking to produce a flyer for our upcoming conference, Lumen 2025. This is an annual conference that we plan to publicize on social media. The ideal designer will create a flyer that is eye-catching and effectively communicates the key information. Please see attached our logo, speaker photo, and flyer content.

Target Market(s)

All demographics

Industry/Entity Type

Christian

Font styles to use
Sans Serif

Requirements
Should not have
• Cross, church

```html
<!DOCTYPE html>
<html lang="en">
<head>
<meta charset="utf-8">
<title>Lumen 2025 Conference Flyer</title>
<link rel="stylesheet" href="https://fonts.googleapis.com/css2?family=Cinzel:wght@400;600;700&family=Montserrat:wght@700;800&family=Open+Sans:wght@400;600;700&family=Orbitron:wght@900&family=Oswald:wght@600&display=swap">
<style>
  :root {
    --page: #cccccc;
    --ink: #030306;
    --card: #0b2a8f;
    --orange: #f6931e;
    --white: #ffffff;
    --navy-text: #132a9a;
  }
  * { margin: 0; padding: 0; box-sizing: border-box; }
  html, body { width: 890px; height: 1200px; overflow: hidden; background: var(--page); }
  .flyer {
    position: absolute; left: 114px; top: 104px; width: 662px; height: 992px;
    background:
      radial-gradient(ellipse 70% 30% at 45% 6%, rgba(20,90,230,0.9), transparent 70%),
      linear-gradient(180deg, #0a3cb8 0%, #062a8a 18%, #04175a 28%, var(--ink) 40%, var(--ink) 100%);
    overflow: hidden; font-family: "Open Sans", sans-serif; color: var(--white);
  }
  .event-title {
    position: absolute; left: 0; width: 100%; top: 28px; text-align: center;
    font-family: "Orbitron", sans-serif; font-weight: 900; font-size: 64px; line-height: 64px;
    color: var(--orange); letter-spacing: 3px;
  }
  .event-subtitle {
    position: absolute; left: 0; width: 100%; top: 92px; text-align: center;
    font-family: "Cinzel", serif; font-weight: 400; font-size: 44px; line-height: 48px; letter-spacing: 0.5px;
  }
  .speaker-photo { position: absolute; left: 300px; top: 165px; width: 362px; height: 500px; }
  .brand {
    position: absolute; left: 46px; top: 214px;
    font-family: "Open Sans", sans-serif; font-weight: 600; font-size: 66px; line-height: 80px;
    color: var(--white); letter-spacing: 1px;
  }
  .label {
    position: absolute; left: 42px; background: var(--orange); color: var(--white);
    font-family: "Montserrat", sans-serif; font-weight: 800; font-size: 21px;
    padding: 0 13px; height: 37px; line-height: 38px; border-radius: 3px;
  }
  .label-topic { top: 345px; }
  .label-speaker { top: 503px; }
  .topic {
    position: absolute; left: 40px; top: 389px; font-family: "Cinzel", serif; font-weight: 400;
    font-size: 46px; line-height: 44px; font-variant: small-caps;
  }
  .topic .accent { color: var(--orange); }
  .speaker-box {
    position: absolute; left: 42px; top: 539px; width: 301px; height: 85px;
    border: 1px solid var(--orange); border-right: none; border-radius: 0 0 0 4px;
    padding: 8px 0 0 14px; font-family: "Cinzel", serif; font-size: 31px; line-height: 35px;
  }
  .schedule { position: absolute; left: 41px; top: 666px; display: flex; gap: 8px; }
  .session {
    width: 193px; height: 63px; background: var(--card); border-radius: 4px;
    text-align: center; font-weight: 700; font-size: 14px; line-height: 19px; padding-top: 12px;
  }
  .session .time { color: var(--orange); }
  .location { position: absolute; left: 41px; top: 760px; font-size: 14.5px; line-height: 19.5px; }
  .location .pin { position: absolute; left: 0; top: 2px; }
  .location h3 { margin-left: 24px; color: var(--orange); font-weight: 700; font-size: 16px; margin-bottom: 5px; }
  .location p { margin-left: 24px; }
  .divider { position: absolute; left: 363px; top: 766px; width: 1.5px; height: 65px; background: var(--orange); }
  .contacts { position: absolute; left: 409px; top: 756px; list-style: none; font-size: 16.5px; }
  .contacts li { display: flex; align-items: center; height: 29.5px; }
  .contacts svg { width: 15px; height: 15px; margin-right: 13px; }
  .contacts .key { color: var(--orange); margin-right: 4px; }
  .app-band {
    position: absolute; left: 0; top: 872px; width: 100%; height: 47px; background: var(--orange);
    text-align: center; font-family: "Oswald", sans-serif; font-weight: 600; font-size: 27px;
    line-height: 47px; color: var(--navy-text); letter-spacing: -0.6px;
  }
  .store-badges { position: absolute; top: 932px; left: 202px; display: flex; gap: 7px; }
  .store-badge { width: 126px; height: 41px; background: var(--white); border-radius: 4px; border: 1px solid #999; }
</style>
</head>
<body>
<main class="flyer">
  <h1 class="event-title">LUMEN 2025</h1>
  <h2 class="event-subtitle">A PROPHETIC CONFERENCE</h2>

  <svg class="speaker-photo" role="img" aria-label="Photo of the speaker in a blue suit" viewBox="0 0 362 500">
    <defs>
      <radialGradient id="suit" cx="60%" cy="62%" r="65%">
        <stop offset="0%" stop-color="#1f5fd0"/>
        <stop offset="55%" stop-color="#123f9a"/>
        <stop offset="100%" stop-color="#030306" stop-opacity="0"/>
      </radialGradient>
    </defs>
    <rect width="362" height="500" fill="url(#suit)"/>
  </svg>

  <div class="brand">HARVEN</div>

  <div class="label label-topic">TOPIC</div>
  <div class="topic">The Voice Of<br><span class="accent">The Lord</span></div>

  <div class="label label-speaker">SPEAKER</div>
  <div class="speaker-box">Prophet<br>Elias Moreno</div>

  <section class="schedule">
    <div class="session">Friday, December 26th,<br><span class="time">6:30 PM - 9:00 PM</span></div>
    <div class="session">Saturday, December 27th,<br><span class="time">5:30 PM - 8:00 PM</span></div>
    <div class="session">Sunday, December 28th,<br><span class="time">4:30 PM - 7:00 PM</span></div>
  </section>

  <section class="location">
    <svg class="pin" width="14" height="19" viewBox="0 0 14 19"><path d="M7 0C3 0 0 3 0 7c0 5 7 12 7 12s7-7 7-12c0-4-3-7-7-7z" fill="#f6931e"/><circle cx="7" cy="7" r="2.6" fill="#030306"/></svg>
    <h3>Location</h3>
    <p>The Brookfield Performing Arts Center,<br>318 Millbrook Street,<br>Brookfield, Maine 04000</p>
  </section>
  <div class="divider"></div>

  <ul class="contacts">
    <li><svg viewBox="0 0 16 16"><path d="M3 1l3 3-2 2c1 2 3 4 5 5l2-2 3 3-2 3C6 15 1 10 0 3z" fill="#f6931e"/></svg><span class="key">Phone:</span>207 555 0142</li>
    <li><svg viewBox="0 0 16 16"><rect x="1" y="3" width="14" height="10" fill="#f6931e"/><path d="M1 3l7 6 7-6" stroke="#030306" stroke-width="1.3" fill="none"/></svg><span class="key">Email:</span>contact@harven.org</li>
    <li><svg viewBox="0 0 16 16"><circle cx="8" cy="8" r="6.5" stroke="#f6931e" stroke-width="1.3" fill="none"/><ellipse cx="8" cy="8" rx="3" ry="6.5" stroke="#f6931e" stroke-width="1.1" fill="none"/><path d="M1.5 8h13M3 4.5h10M3 11.5h10" stroke="#f6931e" stroke-width="1.1"/></svg><span class="key">Website:</span>www.harven.org</li>
  </ul>

  <div class="app-band">Download the HARVEN App to stay updated on the event</div>

  <div class="store-badges">
    <div class="store-badge"></div>
    <div class="store-badge"></div>
  </div>
</main>
</body>
</html>
```